Business Card for beauty technology startup

Design Glimora Business Card for a Beauty, based on the website identity and colors (https://www.glimora-example.com).
Glimora is a beauty tech startup that gathers helpful product info for beauty lovers and consumers (such as availability on stores, price range and product reviews) for makeup products. The card design must be young, colorful but clean, and very modern.

Target Market(s)

woman, 15-35

Industry/Entity Type

Cosmetics

Contact Information for Business Card

Full Name, address, phone

Font styles to use
Other font styles liked:
• Advent Pro

Colors
e34297
86cfc6
ffffff
5c5c5c
e8e8e8
e667a6
b2b2b2

Requirements
Must have
• One full colored side with a creative design and another with card info
• Use Color palette: #95C5C5 and/or #D38AA5
• Use fonts: Advent Pro
• Use website identity: https://www.glimora-example.com
Nice to have
• If needed extra font: Roboto

```html
<!DOCTYPE html>
<html lang="en">
<head>
<meta charset="utf-8">
<title>Glimora Business Card</title>
<link rel="stylesheet" href="https://fonts.googleapis.com/css2?family=Advent+Pro:wght@300;400;500;600&display=swap">
<style>
  :root {
    --backdrop: #e8e8e8;
    --card-pink: #c98099;
    --card-pink-deep: #bc7089;
    --card-white: #f7f7f5;
    --ink: #2b2a2b;
    --accent-pink: #cc7b98;
    --accent-teal: #86c3c0;
    --shadow: rgba(0, 0, 0, 0.18);
  }
  * { margin: 0; padding: 0; box-sizing: border-box; }
  html, body {
    width: 1200px;
    height: 576px;
    overflow: hidden;
    background: var(--backdrop);
  }
  .canvas {
    position: relative;
    width: 1200px;
    height: 576px;
    background: var(--backdrop);
    font-family: "Advent Pro", sans-serif;
  }
  .card {
    position: absolute;
    top: 138px;
    height: 294px;
    border-radius: 11px;
    overflow: hidden;
    box-shadow: 2px 3px 6px var(--shadow);
  }
  /* Front side */
  .card--front {
    left: 82px;
    width: 484px;
    background: linear-gradient(180deg, var(--card-pink) 0%, var(--card-pink-deep) 100%);
  }
  .front-halo {
    position: absolute;
    left: 134px;
    top: 34px;
    width: 224px;
    height: 224px;
    border-radius: 50%;
    border: 10px solid rgba(255, 255, 255, 0.07);
  }
  .brand {
    position: absolute;
    left: 106px;
    top: 119px;
    display: flex;
    align-items: center;
    gap: 16px;
  }
  .brand-dot {
    width: 54px;
    height: 54px;
    border-radius: 50%;
    border: 1.5px solid var(--ink);
  }
  .brand-name {
    font-family: "Advent Pro", sans-serif;
    font-weight: 300;
    font-size: 42px;
    letter-spacing: 5px;
    color: var(--ink);
    line-height: 1;
  }
  /* Back side */
  .card--back {
    left: 602px;
    width: 481px;
    background: var(--card-white);
  }
  .back-ring {
    position: absolute;
    left: -23px;
    top: 10px;
    width: 272px;
    height: 272px;
    border-radius: 50%;
    border: 6px solid var(--accent-pink);
  }
  .contact {
    position: absolute;
    left: 282px;
    top: 83px;
    color: var(--accent-pink);
  }
  .contact-name {
    font-weight: 600;
    font-size: 19px;
    letter-spacing: 0.5px;
    color: var(--accent-teal);
    text-transform: uppercase;
    line-height: 1;
    margin-bottom: 17px;
  }
  .contact-address {
    font-weight: 500;
    font-size: 13px;
    line-height: 16px;
    margin-bottom: 11px;
  }
  .contact-list { list-style: none; }
  .contact-item {
    display: flex;
    align-items: center;
    gap: 9px;
    font-weight: 500;
    font-size: 13px;
    line-height: 16.5px;
  }
  .contact-icon {
    width: 11px;
    height: 11px;
    stroke: var(--accent-teal);
    fill: none;
    stroke-width: 1.6;
    stroke-linecap: round;
    stroke-linejoin: round;
  }
</style>
</head>
<body>
<main class="canvas">
  <section class="card card--front" aria-label="Card front">
    <div class="front-halo"></div>
    <div class="brand">
      <span class="brand-dot"></span>
      <span class="brand-name">GLIMORA</span>
    </div>
  </section>

  <section class="card card--back" aria-label="Card back">
    <div class="back-ring"></div>
    <div class="contact">
      <p class="contact-name">Maya Lindqvist</p>
      <p class="contact-address">123, Street Number, City Name,<br>Country - 123456</p>
      <ul class="contact-list">
        <li class="contact-item">
          <svg class="contact-icon" viewBox="0 0 12 12"><path d="M2.5 1 L4.5 1 L5.2 3.4 L4 4.4 Q5 6.8 7.6 8 L8.6 6.8 L11 7.5 L11 9.5 Q10.5 11 9 11 Q1 10 1 2.8 Q1 1.2 2.5 1 Z"/></svg>
          <span>00 111 222 333</span>
        </li>
        <li class="contact-item">
          <svg class="contact-icon" viewBox="0 0 12 12"><path d="M5 7 L7 5"/><path d="M4.2 5.6 L2.4 7.4 a2 2 0 0 0 2.8 2.8 L7 8.4"/><path d="M7.8 6.4 L9.6 4.6 a2 2 0 0 0 -2.8 -2.8 L5 3.6"/></svg>
          <span>www.glimora-example.com</span>
        </li>
        <li class="contact-item">
          <svg class="contact-icon" viewBox="0 0 12 12"><rect x="1" y="2.5" width="10" height="7"/><path d="M1 2.5 L6 6.5 L11 2.5"/></svg>
          <span>yourname@glimora-example.com</span>
        </li>
      </ul>
    </div>
  </section>
</main>
</body>
</html>
```